Marwick Partners Exit Plan business consultant web site

This website is for a consulting business that helps other businesses with exit plans. Essentially, assists them with the sale of their business. This website should be very professional, almost with a wall street look. I would like a very attractive image on the homepage. Perhaps something that denotes success. Perhaps a picture of palm trees and a beach? I will leave it to you for interpretation.

Across the screen I would like the words "Does your business have an exit plan?"

Below that it should read the following:
Let us help you with a completely impartial, no obligation assessment (button with link to the contact page)

Also, please use logo in a prominent place on the website so it's easily seen.

Target Market(s)

Males 40+

Coding

Coded - Design and coding required

Number of Pages Required

5+ page

Colors

Designer to choose colors to be used in the design.

Requirements
Must have
• The tabs for the homepage on the top should be:
• 1. About us
• 2. Services
• 3. Industries
• 4. Our success
• 5. Contact
Nice to have
• Clean, professional image.
• Please put FB, Twitter, Linked In - logos at bottom.
• Here are two examples of a website to give you an idea:
• https://notes.quelvarocapital.example/library/why-every-business-owner-should-have-an-exit-plan
Should not have
• nothing whimsical or cartoon like

```html
<!DOCTYPE html>
<html lang="en">
<head>
<meta charset="utf-8">
<title>Marwick Partners – Exit Planning Consultants</title>
<link rel="stylesheet" href="https://fonts.googleapis.com/css2?family=Lato:wght@400;700;900&family=Lora:wght@400;500&family=Libre+Baskerville:wght@700&display=swap">
<style>
:root{
  --black:#000;
  --ink:#111;
  --white:#fff;
  --grey-text:#666;
  --grey-line:#ddd;
  --hero-a:#c9d0dc;
  --hero-b:#8d98ad;
  --hero-c:#3c4a66;
  --ind-a:#555a60;
  --ind-b:#2f3338;
  --photo-a:#dfe4ea;
  --photo-b:#9aa2ad;
}
*{margin:0;padding:0;box-sizing:border-box}
html,body{width:1200px;height:3096px;overflow:hidden;background:var(--white)}
body{font-family:"Lato",sans-serif;color:var(--ink);position:relative}
section,header,nav,footer{position:absolute;left:0;width:1200px}
.abs{position:absolute}
a{color:inherit;text-decoration:none}

/* header */
.site-header{top:0;height:105px}
.round-icon{width:44px;height:44px;border:1px solid #ccc;border-radius:50%;display:flex;align-items:center;justify-content:center;background:#fff}
.header-phone{left:112px;top:29px}
.header-phone-text{left:181px;top:34px;font-size:26px;color:#555;font-weight:400}
.brand{left:480px;top:8px;width:240px;text-align:center}
.brand-mark{width:50px;height:62px;background:var(--black);margin:0 auto 8px}
.brand-name{font-family:"Lato",sans-serif;font-size:17px;line-height:20px;letter-spacing:1px;color:#222;text-transform:uppercase;white-space:nowrap}
.header-mail{left:852px;top:29px}
.header-mail-text{left:920px;top:42px;font-size:15px;color:#555}

/* nav */
.main-nav{top:105px;height:54px;background:var(--black)}
.main-nav a{position:absolute;top:0;line-height:54px;color:var(--white);font-weight:900;font-size:16px;text-transform:uppercase}
.main-nav .active{left:112px;width:109px;text-align:center;color:#222;background:linear-gradient(#aaa,#f2f2f2 55%,#ccc)}

/* hero */
.hero{top:159px;height:560px;background:linear-gradient(100deg,var(--hero-a) 0%,var(--hero-b) 45%,var(--hero-c) 80%,#26324a 100%)}
.hero-title{left:112px;top:96px;font-family:"Libre Baskerville",serif;font-weight:700;font-size:56px;line-height:68px;color:var(--white)}
.hero-title .dark{color:var(--black)}
.hero-sub{left:112px;top:316px;font-size:17px;font-weight:900;line-height:29px;color:var(--white);text-transform:uppercase}
.btn{display:flex;align-items:center;justify-content:center;gap:10px;width:176px;height:56px;background:var(--black);color:var(--white);font-weight:900;font-size:16px;text-transform:uppercase;outline:2px solid var(--white);outline-offset:-6px}
.hero .btn{left:112px;top:398px}
.slider-dots{left:560px;top:478px;display:flex;gap:8px}
.slider-dots span{width:14px;height:14px;border:2px solid var(--black);background:var(--white);transform:rotate(45deg);box-shadow:inset 0 0 0 2px #fff, inset 0 0 0 5px #000}

/* headings */
.section-title{font-family:"Lora",serif;font-weight:400;font-size:42px;line-height:50px}
.rule{width:62px;height:4px;background:var(--black)}

/* services */
.services{top:719px;height:889px}
.services .section-title{left:0;width:1200px;text-align:center;top:100px}
.services .rule{left:569px;top:157px}
.services-intro{left:260px;width:680px;top:194px;text-align:center;font-size:15px;line-height:30px;color:var(--grey-text)}
.service-card{width:214px;height:255px;border:2px solid #eee;background:#fff;padding:5px;box-shadow:0 2px 6px rgba(0,0,0,.08)}
.service-card .inner{height:100%;border:3px solid var(--black);text-align:center;padding-top:30px}
.service-icon{width:62px;height:62px;margin:0 auto;background:#d8d8d8;border-radius:4px}
.service-card h3{font-size:15px;font-weight:900;margin:26px 0 10px;color:#222}
.service-card p{font-size:14px;line-height:23px;color:var(--grey-text)}
.carousel-arrow{width:40px;height:40px;border:1px solid #ccc;border-radius:50%;background:#fff;display:flex;align-items:center;justify-content:center}
.services .btn{left:512px;top:705px}

/* industries */
.industries{top:1608px;height:514px;background:linear-gradient(100deg,var(--ind-a),#6b7078 50%,var(--ind-b))}
.industry-tile{width:217px;height:168px;background:var(--white);text-align:center;padding-top:28px}
.industry-icon{width:66px;height:66px;margin:0 auto;background:#d8d8d8;border-radius:4px}
.industry-tile h3{margin-top:24px;font-size:15px;font-weight:900;color:#222}
.industries .section-title{left:664px;top:58px;color:var(--white);font-size:40px}
.industries .rule{left:669px;top:115px;background:var(--white)}
.industries-text{left:664px;top:150px;width:424px;font-size:15px;line-height:34.3px;color:var(--white);text-align:justify}
.industries .btn{left:664px;top:394px}

/* success */
.success{top:2122px;height:640px}
.success .section-title{left:110px;top:120px}
.success .rule{left:116px;top:175px}
.success-text{left:110px;top:212px;width:463px;font-size:15px;line-height:37px;color:var(--grey-text);text-align:justify}
.success .btn{left:110px;top:450px}
.photo-side{top:187px;height:258px;background:linear-gradient(90deg,#c4cad2,#eef1f4)}
.photo-main{left:719px;top:122px;width:317px;height:389px;background:#fff;padding:9px;box-shadow:0 2px 8px rgba(0,0,0,.15)}
.photo-main div{width:100%;height:100%;background:linear-gradient(160deg,var(--photo-a),#c1c7cf 50%,var(--photo-b))}
.success .carousel-arrow{top:295px}

/* footer */
.site-footer{top:2762px;height:334px;background:var(--black);color:var(--white)}
.footer-col h4{font-size:15px;font-weight:900;text-decoration:underline;text-transform:uppercase;margin-bottom:16px}
.footer-about p{font-size:14px;line-height:30px;font-weight:700;width:262px;text-align:justify}
.footer-about a{display:inline-block;margin-top:12px;font-size:15px;text-decoration:underline}
.footer-links li{list-style:none;font-size:13px;line-height:34px}
.footer-links li::before{content:"»";margin-right:12px;font-weight:900}
.contact-row{display:flex;align-items:center;gap:18px;font-size:13px;line-height:20px;margin-bottom:22px}
.contact-row .dot{width:30px;height:30px;border-radius:50%;background:var(--white);display:flex;align-items:center;justify-content:center;flex:none}
.footer-rule{left:110px;top:274px;width:978px;height:1px;background:#888}
.copyright{left:110px;top:296px;font-size:15px}
.social{top:288px;width:36px;height:36px;border:2px solid var(--white);border-radius:50%;display:flex;align-items:center;justify-content:center}
</style>
</head>
<body>

<header class="site-header">
  <div class="abs round-icon header-phone"><svg width="18" height="18" viewBox="0 0 24 24"><path d="M6.6 10.8a15 15 0 0 0 6.6 6.6l2.2-2.2a1 1 0 0 1 1-.25 11 11 0 0 0 3.6.6 1 1 0 0 1 1 1V20a1 1 0 0 1-1 1A17 17 0 0 1 3 4a1 1 0 0 1 1-1h3.5a1 1 0 0 1 1 1c0 1.25.2 2.45.6 3.6a1 1 0 0 1-.25 1z" fill="#111"/></svg></div>
  <div class="abs header-phone-text">555 014 2290</div>
  <a class="abs brand" href="#"><div class="brand-mark"></div><div class="brand-name">Marwick Partners</div></a>
  <div class="abs round-icon header-mail"><svg width="18" height="14" viewBox="0 0 18 14"><rect x="1" y="1" width="16" height="12" rx="2" fill="none" stroke="#111" stroke-width="1.6"/><path d="M1.5 2 9 8l7.5-6" fill="none" stroke="#111" stroke-width="1.6"/></svg></div>
  <div class="abs header-mail-text">info@marwickpartners.example</div>
</header>

<nav class="main-nav">
  <a class="active" href="#">Home</a>
  <a href="#" style="left:316px">About Us</a>
  <a href="#" style="left:464px">Services</a>
  <a href="#" style="left:606px">Industries</a>
  <a href="#" style="left:766px">Our Success</a>
  <a href="#" style="left:939px">Contact</a>
</nav>

<section class="hero" role="img" aria-label="Photo of two smiling businessmen in suits working at a laptop">
  <h1 class="abs hero-title">DOES YOUR<br><span class="dark">BUSINESS</span> HAVE<br>AN EXIT PLAN</h1>
  <p class="abs hero-sub">Let us help you with a completely impartial,<br>no obligation assessment</p>
  <a class="abs btn" href="#">Contact Us <svg width="14" height="14" viewBox="0 0 14 14"><circle cx="7" cy="7" r="7" fill="#fff"/><path d="M5.5 4 8.5 7l-3 3" fill="none" stroke="#000" stroke-width="2"/></svg></a>
  <div class="abs slider-dots"><span></span><span></span><span></span></div>
</section>

<section class="services">
  <h2 class="abs section-title">Our Services</h2>
  <div class="abs rule"></div>
  <p class="abs services-intro">At vero eos et accusamus et iusto odio dignissimos ducimus qui blanditiis praesentium voluptatum deleniti atque corrupti quos dolores et quas molestias excepturi sint occaecati.</p>

  <div class="abs carousel-arrow" style="left:33px;top:432px"><svg width="12" height="16" viewBox="0 0 12 16"><path d="M9 2 3 8l6 6" fill="none" stroke="#111" stroke-width="2.4"/></svg></div>
  <div class="abs carousel-arrow" style="left:1132px;top:432px"><svg width="12" height="16" viewBox="0 0 12 16"><path d="m3 2 6 6-6 6" fill="none" stroke="#111" stroke-width="2.4"/></svg></div>

  <article class="abs service-card" style="left:144px;top:322px"><div class="inner"><div class="service-icon" role="img" aria-label="Line icon of a consultant with tools"></div><h3>LOREM IPSUM DOLOR</h3><p>Sed ut perspiciatis<br>unde omnis iste natus error<br>sit voluptatem accusan.</p></div></article>
  <article class="abs service-card" style="left:378px;top:363px"><div class="inner"><div class="service-icon" role="img" aria-label="Line icon of a presentation meeting"></div><h3>LOREM IPSUM DOLOR</h3><p>Sed ut perspiciatis<br>unde omnis iste natus error<br>sit voluptatem accusan.</p></div></article>
  <article class="abs service-card" style="left:610px;top:322px"><div class="inner"><div class="service-icon" role="img" aria-label="Line icon of an advisor with client profile"></div><h3>LOREM IPSUM DOLOR</h3><p>Sed ut perspiciatis<br>unde omnis iste natus error<br>sit voluptatem accusan.</p></div></article>
  <article class="abs service-card" style="left:843px;top:363px"><div class="inner"><div class="service-icon" role="img" aria-label="Line icon of a team at a computer"></div><h3>LOREM IPSUM DOLOR</h3><p>Sed ut perspiciatis<br>unde omnis iste natus error<br>sit voluptatem accusan.</p></div></article>

  <a class="abs btn" href="#">View All <svg width="14" height="14" viewBox="0 0 14 14"><circle cx="7" cy="7" r="7" fill="#fff"/><path d="M5.5 4 8.5 7l-3 3" fill="none" stroke="#000" stroke-width="2"/></svg></a>
</section>

<section class="industries" role="img" aria-label="Photo of a modern glass-walled office interior">
  <div class="abs industry-tile" style="left:115px;top:62px"><div class="industry-icon" role="img" aria-label="Line icon of a warehouse"></div><h3>LOREM IPSUM DOLOR</h3></div>
  <div class="abs industry-tile" style="left:360px;top:89px"><div class="industry-icon" role="img" aria-label="Line icon of a person at a desk"></div><h3>LOREM IPSUM DOLOR</h3></div>
  <div class="abs industry-tile" style="left:115px;top:259px"><div class="industry-icon" role="img" aria-label="Line icon of a finance advisor"></div><h3>LOREM IPSUM DOLOR</h3></div>
  <div class="abs industry-tile" style="left:360px;top:286px"><div class="industry-icon" role="img" aria-label="Line icon of a group of people"></div><h3>LOREM IPSUM DOLOR</h3></div>
  <h2 class="abs section-title">Our Industries</h2>
  <div class="abs rule"></div>
  <p class="abs industries-text">At vero eos et accusamus et iusto odio dignissimos ducimus qui blanditiis praesentium voluptatum deleniti atque corrupti quos dolores et quas molestias excepturi sint occaecati cupiditate non provident, similique sunt in culpa qui officia deserunt mollitia animi, id est laborum et dolorum fuga. At vero eos et accusamus et iusto odio dignissimos ducimus qui blanditiis.</p>
  <a class="abs btn" href="#">Read More <svg width="14" height="14" viewBox="0 0 14 14"><circle cx="7" cy="7" r="7" fill="#fff"/><path d="M5.5 4 8.5 7l-3 3" fill="none" stroke="#000" stroke-width="2"/></svg></a>
</section>

<section class="success">
  <h2 class="abs section-title">Our Success Stories</h2>
  <div class="abs rule"></div>
  <p class="abs success-text">Sed ut perspiciatis unde omnis iste natus error sit voluptatem accusantium doloremque laudantium, totam rem aperiam, eaque ipsa quae ab illo inventore veritatis et quasi architecto beatae vitae dicta sunt explicabo. Nemo enim ipsam voluptatem quia voluptas sit aspernatur aut odit aut fugit, sed quia consequuntur.Sed ut perspiciatis unde omnis iste natus.</p>
  <a class="abs btn" href="#">Read More <svg width="14" height="14" viewBox="0 0 14 14"><circle cx="7" cy="7" r="7" fill="#fff"/><path d="M5.5 4 8.5 7l-3 3" fill="none" stroke="#000" stroke-width="2"/></svg></a>
  <div class="abs photo-side" style="left:670px;width:60px" role="img" aria-label="Client portrait, previous slide"></div>
  <div class="abs photo-side" style="left:1026px;width:60px" role="img" aria-label="Client portrait, next slide"></div>
  <div class="abs photo-main"><div role="img" aria-label="Portrait photo of a smiling businessman in a dark suit with arms crossed"></div></div>
  <div class="abs carousel-arrow" style="left:700px"><svg width="12" height="16" viewBox="0 0 12 16"><path d="M9 2 3 8l6 6" fill="none" stroke="#111" stroke-width="2.4"/></svg></div>
  <div class="abs carousel-arrow" style="left:1014px"><svg width="12" height="16" viewBox="0 0 12 16"><path d="m3 2 6 6-6 6" fill="none" stroke="#111" stroke-width="2.4"/></svg></div>
</section>

<footer class="site-footer">
  <div class="abs footer-col footer-about" style="left:123px;top:46px">
    <h4>About Us</h4>
    <p>Lorem ipsum dolor sit amet, consectetur adipiscing elit, sed do eiusmod tempor incididunt ut labore et dolore magna aliquaUt enim ad minim.</p>
    <a href="#">READ MORE »</a>
  </div>
  <div class="abs footer-col" style="left:463px;top:46px">
    <h4>Quick Links</h4>
    <ul class="footer-links"><li>Home</li><li>About Us</li><li>Services</li><li>Reviews</li><li>Contact Us</li></ul>
  </div>
  <div class="abs footer-col" style="left:660px;top:46px">
    <h4>Other Links</h4>
    <ul class="footer-links"><li>FAQ</li><li>Help Service</li><li>Terms Of Use</li><li>Privacy Policy</li><li>Blog</li></ul>
  </div>
  <div class="abs footer-col" style="left:868px;top:46px">
    <h4>Contact Us</h4>
    <div class="contact-row"><span class="dot"><svg width="12" height="16" viewBox="0 0 12 16"><path d="M6 0a6 6 0 0 0-6 6c0 4.5 6 10 6 10s6-5.5 6-10a6 6 0 0 0-6-6zm0 8.5A2.5 2.5 0 1 1 6 3.5a2.5 2.5 0 0 1 0 5z" fill="#000"/></svg></span><span>639 , Nemo enim ipsam<br>United States</span></div>
    <div class="contact-row"><span class="dot"><svg width="14" height="14" viewBox="0 0 24 24"><path d="M6.6 10.8a15 15 0 0 0 6.6 6.6l2.2-2.2a1 1 0 0 1 1-.25 11 11 0 0 0 3.6.6 1 1 0 0 1 1 1V20a1 1 0 0 1-1 1A17 17 0 0 1 3 4a1 1 0 0 1 1-1h3.5a1 1 0 0 1 1 1c0 1.25.2 2.45.6 3.6a1 1 0 0 1-.25 1z" fill="#000"/></svg></span><span>555 014 2290</span></div>
    <div class="contact-row"><span class="dot"><svg width="14" height="11" viewBox="0 0 18 14"><rect x="1" y="1" width="16" height="12" rx="2" fill="none" stroke="#000" stroke-width="1.8"/><path d="M1.5 2 9 8l7.5-6" fill="none" stroke="#000" stroke-width="1.8"/></svg></span><span>info@marwickpartners.example</span></div>
  </div>
  <div class="abs footer-rule"></div>
  <p class="abs copyright">© 2020 Marwick Partners. All Rights Reserved</p>
  <a class="abs social" href="#" style="left:958px" aria-label="Social profile"><svg width="16" height="16" viewBox="0 0 16 16"><circle cx="12" cy="3" r="2.2" fill="#fff"/><circle cx="4" cy="8" r="2.2" fill="#fff"/><circle cx="12" cy="13" r="2.2" fill="#fff"/><path d="M12 3 4 8l8 5" fill="none" stroke="#fff" stroke-width="1.4"/></svg></a>
  <a class="abs social" href="#" style="left:1005px" aria-label="Social profile"><svg width="16" height="16" viewBox="0 0 16 16"><circle cx="12" cy="3" r="2.2" fill="#fff"/><circle cx="4" cy="8" r="2.2" fill="#fff"/><circle cx="12" cy="13" r="2.2" fill="#fff"/><path d="M12 3 4 8l8 5" fill="none" stroke="#fff" stroke-width="1.4"/></svg></a>
  <a class="abs social" href="#" style="left:1052px" aria-label="Social profile"><svg width="16" height="16" viewBox="0 0 16 16"><circle cx="12" cy="3" r="2.2" fill="#fff"/><circle cx="4" cy="8" r="2.2" fill="#fff"/><circle cx="12" cy="13" r="2.2" fill="#fff"/><path d="M12 3 4 8l8 5" fill="none" stroke="#fff" stroke-width="1.4"/></svg></a>
</footer>

</body>
</html>
```